Business Card Design for Occupational Medicine Start Up Company

We need to design a professional business card. We are a healthcare company providing occupational medicine services to blue collar industries. We are professional, efficient and high quality service providers.

Target Market(s)

Blue Collar Industry: Shipbuilding, Ports, Trucking Companies; The Executives and Safety Officers for these companies

Industry/Entity Type

Healthcare

Contact Information for Business Card

Logo, Name, Title, Email, Phone

Other font styles liked:
• Please match our Brand Guide

Requirements
Must have
• Our Company Colors and Logo

```html
<!DOCTYPE html>
<html lang="en">
<head>
<meta charset="utf-8">
<title>Harborwell Business Card</title>
<link href="https://fonts.googleapis.com/css2?family=Montserrat:wght@400;500;600;700&display=swap" rel="stylesheet">
<style>
  :root {
    --sky: #22a6de;
    --navy: #2b3585;
    --amber: #f5a533;
    --paper: #ffffff;
    --ink: #2f3140;
    --rule: #ececec;
    --backdrop: #f2f2f2;
  }
  html, body {
    margin: 0;
    padding: 0;
    width: 1200px;
    height: 2643px;
    overflow: hidden;
    background: var(--backdrop);
    font-family: "Montserrat", sans-serif;
  }
  .canvas {
    position: relative;
    width: 1200px;
    height: 2643px;
  }
  .card {
    position: absolute;
    left: 330px;
    width: 540px;
    height: 945px;
    background: var(--paper);
    box-shadow: 0 10px 24px rgba(0, 0, 0, 0.18);
  }
  .card svg { display: block; width: 100%; height: 100%; }
  .card-front { top: 300px; }
  .card-back { top: 1400px; }
  .band { fill: var(--sky); }
  .dot { fill: var(--navy); }
  .ring { fill: var(--paper); }
  .ring-accent { fill: var(--amber); }
  .brand-name {
    font-family: "Montserrat", sans-serif;
    font-weight: 600;
    fill: var(--navy);
    letter-spacing: 1px;
  }
  .web-address {
    font-family: "Montserrat", sans-serif;
    font-weight: 700;
    fill: var(--paper);
    font-size: 22px;
    letter-spacing: 1.6px;
  }
  .person-name {
    font-family: "Montserrat", sans-serif;
    font-weight: 700;
    fill: var(--sky);
    font-size: 37px;
  }
  .title-box { fill: var(--navy); }
  .title-text {
    font-family: "Montserrat", sans-serif;
    font-weight: 700;
    fill: var(--paper);
    font-size: 14.5px;
  }
  .divider { stroke: var(--rule); stroke-width: 6; stroke-linecap: round; }
  .contact-icon { fill: var(--sky); }
  .icon-glyph { fill: none; stroke: var(--paper); stroke-width: 1.6; stroke-linecap: round; stroke-linejoin: round; }
  .contact-text {
    font-family: "Montserrat", sans-serif;
    font-weight: 500;
    fill: var(--ink);
    font-size: 16px;
  }
</style>
</head>
<body>
<main class="canvas">

  <section class="card card-front" aria-label="Business card front">
    <svg viewBox="0 0 420 735" xmlns="http://www.w3.org/2000/svg">
      <rect class="band" x="0" y="540" width="420" height="195"/>

      <circle class="ring" cx="157" cy="540" r="21"/>
      <circle class="dot" cx="157" cy="540" r="17"/>

      <circle class="ring-accent" cx="364" cy="546" r="52"/>
      <circle class="ring" cx="362" cy="540" r="52"/>
      <circle class="dot" cx="362" cy="540" r="47"/>

      <circle class="dot" cx="210" cy="290" r="34"/>
      <text class="brand-name" x="210" y="404" text-anchor="middle" font-size="34">HARBORWELL</text>

      <text class="web-address" x="212" y="660" text-anchor="middle">www.harborwell.com</text>
    </svg>
  </section>

  <section class="card card-back" aria-label="Business card back">
    <svg viewBox="0 0 420 735" xmlns="http://www.w3.org/2000/svg">
      <rect class="band" x="0" y="0" width="420" height="82"/>

      <circle class="ring" cx="83" cy="82" r="21"/>
      <circle class="dot" cx="83" cy="82" r="17"/>

      <circle class="ring" cx="288" cy="82" r="52"/>
      <circle class="ring-accent" cx="288" cy="78" r="50"/>
      <circle class="dot" cx="288" cy="84" r="47"/>

      <circle class="dot" cx="210" cy="236" r="24"/>
      <text class="brand-name" x="210" y="303" text-anchor="middle" font-size="28">HARBORWELL</text>

      <text class="person-name" x="208" y="389" text-anchor="middle">DANA WHITFIELD</text>
      <rect class="title-box" x="88" y="402" width="233" height="26"/>
      <text class="title-text" x="204.5" y="420" text-anchor="middle">CHIEF EXECUTIVE OFFICER</text>

      <line class="divider" x1="60" y1="456" x2="346" y2="456"/>

      <g class="contact-row">
        <circle class="contact-icon" cx="73" cy="532" r="12"/>
        <path class="icon-glyph" d="M68 527c0 6 4 10 10 10l1.5-2.5-2.5-2-1.5 1.2c-1.6-.8-2.9-2.1-3.7-3.7l1.2-1.5-2-2.5z"/>
        <text class="contact-text" x="95" y="538">+1 (555) 013-2290</text>
      </g>
      <g class="contact-row">
        <circle class="contact-icon" cx="73" cy="564" r="12"/>
        <rect class="icon-glyph" x="66.5" y="559.5" width="13" height="9" rx="1"/>
        <path class="icon-glyph" d="M66.5 560.5l6.5 4.5 6.5-4.5"/>
        <text class="contact-text" x="98" y="570">info@harborwell.com</text>
      </g>
      <g class="contact-row">
        <circle class="contact-icon" cx="73" cy="600" r="12"/>
        <path class="icon-glyph" d="M73 608c-3.5-4-5.5-6.5-5.5-9a5.5 5.5 0 0 1 11 0c0 2.5-2 5-5.5 9z"/>
        <circle class="icon-glyph" cx="73" cy="599" r="1.8"/>
        <text class="contact-text" x="98" y="597">Quayside Park, 1800, 9Th Floors</text>
        <text class="contact-text" x="98" y="618">Port City - United State</text>
      </g>
      <g class="contact-row">
        <circle class="contact-icon" cx="73" cy="645" r="12"/>
        <circle class="icon-glyph" cx="73" cy="645" r="6.5"/>
        <ellipse class="icon-glyph" cx="73" cy="645" rx="2.8" ry="6.5"/>
        <path class="icon-glyph" d="M66.5 645h13"/>
        <text class="contact-text" x="98" y="651">www.harborwell.com</text>
      </g>
    </svg>
  </section>

</main>
</body>
</html>
```